Mobile Fitness snd Therapy Business Card Design

I need a business card designed for my mobile fitness and therapy business.

Please view the images that I have uploaded. I like the simplicity of the design that I have attached. I adapted it with my information

Target Market(s)

Those seeking personal training, injury rehabilitation or massage therapy.

Industry/Entity Type

Business

Contact Information for Business Card

Derek Fulham - MSc, CAT(C), RMT, CSCS, Pn2
e-mail: derek@vantrelo.com
website: www.vantrelo.com
instagram: @derek_fulham

Font styles to use
Sans Serif

Colors
3176b5
0355a3

Requirements
Must have
• "Contact us to receive a FREE assessment"
• Services offered:
• Personal Training
• Golf Fitness
• Injury Rehab
• Massage Therapy
• Yoga
Nice to have
• Consistent colours with brand
• - Dark Blue: #232837
• - Blue: #5096f0
• Consistent look/feel with the website: www.vantrelo.com

```html
<!DOCTYPE html>
<html lang="en">
<head>
<meta charset="utf-8">
<title>Vantrelo Business Card</title>
<link href="https://fonts.googleapis.com/css2?family=Arimo:wght@400;700&display=swap" rel="stylesheet">
<style>
  :root {
    --dark-blue: #232837;
    --brand-blue: #5096f0;
    --deep-blue: #2459c9;
    --action-blue: #1f5bd6;
    --light-blue: #7fb3f0;
    --mid-blue: #4f8fe6;
    --white: #ffffff;
    --page: #e9ecf1;
  }
  * { margin: 0; padding: 0; box-sizing: border-box; }
  html, body {
    width: 1200px; height: 900px; overflow: hidden;
    background: var(--page);
    font-family: "Arimo", Arial, sans-serif;
  }
  .canvas { position: relative; width: 1200px; height: 900px; }

  .card {
    position: absolute;
    border-radius: 14px;
    overflow: hidden;
    box-shadow: 0 6px 20px rgba(20, 30, 50, 0.18);
  }

  /* Front */
  .card-front {
    left: 177px; top: 74px; width: 590px; height: 364px;
    background: var(--dark-blue);
    color: var(--white);
  }
  .front-panel {
    position: absolute; left: 0; top: 0; width: 305px; height: 100%;
    background: linear-gradient(160deg, #2a5fd6 0%, var(--brand-blue) 55%, #8ab9f5 100%);
    border-radius: 0 36px 36px 0;
  }
  .front-info {
    position: absolute; right: 37px; top: 50px;
    text-align: right;
  }
  .person-name { font-size: 22px; font-weight: 700; letter-spacing: 0.3px; line-height: 26px; }
  .credentials { font-size: 14px; margin-top: 8px; line-height: 18px; }
  .contact-list { list-style: none; margin-top: 16px; }
  .contact-list li {
    font-size: 17px; line-height: 24.5px;
    display: flex; justify-content: flex-end; align-items: center; gap: 6px;
  }
  .contact-icon { width: 15px; height: 15px; flex: none; }

  .service-list {
    list-style: none; position: absolute; right: 37px; top: 236px; text-align: right;
  }
  .service-list li {
    font-size: 15px; line-height: 19px;
    display: flex; justify-content: flex-end; align-items: center; gap: 6px;
  }
  .service-mark { width: 9px; height: 9px; background: var(--white); flex: none; }

  /* Back */
  .card-back {
    left: 388px; top: 505px; width: 567px; height: 352px;
    background: var(--white);
  }
  .brand-block {
    position: absolute; left: 0; right: 0; top: 136px; text-align: center;
  }
  .brand-name {
    font-size: 42px; font-weight: 700; letter-spacing: 6px;
    color: var(--dark-blue); line-height: 46px;
  }
  .brand-tagline {
    font-size: 14px; font-weight: 700; letter-spacing: 2.4px;
    color: var(--dark-blue); margin-top: 4px;
  }
  .offer-bar {
    position: absolute; left: 106px; top: 279px; width: 355px; height: 5px;
    display: flex; gap: 2px;
  }
  .offer-bar span { flex: 1; border-radius: 3px; }
  .offer-bar .seg-light { background: var(--light-blue); }
  .offer-bar .seg-mid { background: var(--mid-blue); }
  .offer-bar .seg-deep { background: var(--deep-blue); }
  .offer-text {
    position: absolute; left: 0; right: 0; top: 295px; text-align: center;
    font-size: 14.5px; font-weight: 700; color: var(--action-blue); letter-spacing: 0.2px;
  }
</style>
</head>
<body>
<div class="canvas">

  <section class="card card-front">
    <div class="front-panel" role="img" aria-label="Blue gradient brand panel"></div>

    <div class="front-info">
      <h1 class="person-name">DEREK FULHAM</h1>
      <p class="credentials">MSc, CAT(C), RMT, CSCS, Pn2</p>
      <ul class="contact-list">
        <li>derek@vantrelo.com
          <svg class="contact-icon" viewBox="0 0 16 16" aria-hidden="true">
            <rect x="1" y="3" width="14" height="10" fill="none" stroke="#fff" stroke-width="1.5"/>
            <path d="M1 3 L8 9 L15 3" fill="none" stroke="#fff" stroke-width="1.5"/>
          </svg>
        </li>
        <li>www.vantrelo.com
          <svg class="contact-icon" viewBox="0 0 16 16" aria-hidden="true">
            <circle cx="8" cy="8" r="6.5" fill="none" stroke="#fff" stroke-width="1.5"/>
            <ellipse cx="8" cy="8" rx="2.8" ry="6.5" fill="none" stroke="#fff" stroke-width="1.2"/>
            <line x1="1.5" y1="8" x2="14.5" y2="8" stroke="#fff" stroke-width="1.2"/>
          </svg>
        </li>
        <li>@derek_fulham
          <svg class="contact-icon" viewBox="0 0 16 16" aria-hidden="true">
            <rect x="1.5" y="1.5" width="13" height="13" rx="2" fill="#fff"/>
          </svg>
        </li>
      </ul>
    </div>

    <ul class="service-list">
      <li>Personal Training <span class="service-mark"></span></li>
      <li>Golf Fitness <span class="service-mark"></span></li>
      <li>Injury Rehab <span class="service-mark"></span></li>
      <li>Massage Therapy <span class="service-mark"></span></li>
      <li>Yoga <span class="service-mark"></span></li>
    </ul>
  </section>

  <section class="card card-back">
    <div class="brand-block">
      <h2 class="brand-name">VANTRELO</h2>
      <p class="brand-tagline">NUTRITION - FITNESS - HEALTH</p>
    </div>
    <div class="offer-bar">
      <span class="seg-light"></span><span class="seg-mid"></span><span class="seg-deep"></span>
    </div>
    <p class="offer-text">CONTACT US TO RECEIVE&nbsp; A FREE ASSESSMENT</p>
  </section>

</div>
</body>
</html>
```